RV7 - Rapid Vigil Field Operations Suite

I need an introductory website for RV7 which describes the features of the product and the ease of use of the product. The product is focused on Preparing for an incident using Volunteer and Resource management and then responding to an incident with Incident Management, Team Management, Task Management and Communication Management. Once a situation is handled, the application provides complete reporting on each of the above aspects

Target Market(s)

Local Government entities, specifically the emergency department directors or coordinators

Industry/Entity Type

Government Office

Coding

Coded - Design and coding required

Font styles to use
Sans Serif

Requirements
Must have
• Clear layout with modern images. I want to be able to get a clear understanding of the features of the product and the ease of use. I would like to high light how the application helps in Communication Management, Team Management, Task Management and Incident Managements. Also, how the use of application helps to get an immediate snap shot of how well an incident was handled. I want to highlight how the Dashboard provides a quick look at the Incident(s) being managed
Nice to have
• I would like to in the future add videos to the site. At this point don't have any ideas about nice to have features
Should not have
• traditional designs. I am looking for a slick, modern looking website. Clean design is the key.

```html
<!DOCTYPE html>
<html lang="en">
<head>
<meta charset="utf-8">
<title>RV7 - Rapid Vigil Field Operations Suite</title>
<link href="https://fonts.googleapis.com/css2?family=Roboto:wght@300;400;500;700&family=Open+Sans:wght@400;600&display=swap" rel="stylesheet">
<style>
:root{
  --blue:#1c6db3;
  --blue-band:#2f7cc2;
  --blue-deep:#1a5a99;
  --green:#a9d13b;
  --green-light:#c6e365;
  --green-dark:#7fae1f;
  --ink:#222;
  --muted:#666;
  --grey-bg:#f2f2f2;
  --footer:#262626;
  --footer-deep:#141414;
  --white:#fff;
}
*{box-sizing:border-box;margin:0;padding:0}
html,body{width:1200px;height:3600px;overflow:hidden}
body{font-family:"Open Sans",sans-serif;color:var(--ink);background:var(--white);position:relative}
h1,h2,h3,.nav,.btn{font-family:"Roboto",sans-serif}
.abs{position:absolute}

/* header */
.site-header{position:absolute;left:0;top:0;width:1200px;height:144px;background:var(--white)}
.brand{position:absolute;left:100px;top:36px;display:flex;align-items:center;gap:18px}
.brand-mark{width:60px;height:60px;border-radius:50%;background:var(--blue)}
.brand-name{font-family:"Roboto",sans-serif;font-weight:500;font-size:46px;color:var(--ink);letter-spacing:1px}
.nav{position:absolute;right:115px;top:74px;display:flex;gap:22px;font-size:12.5px;color:#333;letter-spacing:.3px}

/* hero */
.hero{position:absolute;left:0;top:144px;width:1200px;height:622px;
  background:linear-gradient(100deg,#c9d6dd 0%,#e3ebef 40%,#d5e0e6 70%,#b9c7cf 100%)}
.hero-title{position:absolute;left:560px;top:268px;width:530px;text-align:right;font-weight:300;font-size:46px;line-height:60px;color:#111}
.btn{display:flex;align-items:center;justify-content:center;background:var(--blue);color:var(--white);font-size:20px}
.hero .btn{position:absolute;left:696px;top:422px;width:252px;height:56px}

/* why adopt */
.section-title{position:absolute;left:0;width:1200px;text-align:center;font-family:"Roboto",sans-serif;font-weight:300;font-size:38px;color:#222}
.why-list{position:absolute;left:112px;top:900px;width:520px;list-style:none;font-size:12.5px;color:#333}
.why-list li{display:flex;align-items:center;gap:14px;height:31px}
.why-list li.sub{padding-left:40px}
.tick{width:14px;height:14px;flex:none}
.why-image{position:absolute;left:636px;top:896px;width:564px;height:422px;
  background:linear-gradient(135deg,#d9d2c1 0%,#e7e0cd 35%,#f0e83a 60%,#e9d900 100%)}

/* tasks */
.tasks{position:absolute;left:0;top:1382px;width:1200px;height:500px;background:linear-gradient(180deg,var(--blue-band),var(--blue-deep))}
.tasks .section-title{color:var(--white);top:60px}
.task-card{position:absolute;left:70px;top:208px;width:1065px;height:188px;background:var(--white);display:flex;gap:14px;padding:10px 10px 0}
.task{flex:1;text-align:center}
.task-photo{height:170px}
.task-name{font-family:"Roboto",sans-serif;font-size:19px;color:#222;margin-top:12px}

/* what we do */
.what-sub{position:absolute;left:0;top:1990px;width:1200px;text-align:center;font-size:13px;color:#999}
.feature{position:absolute;top:2062px;width:242px;height:262px;background:linear-gradient(180deg,var(--green-light),var(--green));border-radius:0 34px 0 34px;overflow:hidden}
.feature h3{height:70px;display:flex;align-items:center;justify-content:center;font-size:14px;font-weight:700;color:#1a1a1a;letter-spacing:.3px;background:rgba(255,255,255,.18)}
.feature ul{list-style:none;padding:24px 0 0 50px;font-size:12.5px;color:#222}
.feature li{display:flex;gap:12px;align-items:flex-start;line-height:18px;margin-bottom:9px}

/* mobile screens */
.screens{position:absolute;left:0;top:2396px;width:1200px;height:704px;background:var(--grey-bg)}
.screens .section-title{top:50px}
.phone{position:absolute;top:137px;background:var(--white);box-shadow:0 2px 8px rgba(0,0,0,.25);font-family:"Roboto",sans-serif;overflow:hidden}
.statusbar{height:18px;font-size:9px;color:#fff;text-align:right;padding:3px 8px}
.appbar{height:38px;background:var(--blue);color:#fff;font-size:13px;display:flex;align-items:center;padding-left:40px}
.drawer{position:absolute;left:0;top:0;width:190px;height:100%;background:#1d76c9;color:#fff}
.drawer-head{height:120px;padding:50px 0 0 16px;font-size:14px;font-weight:700;background:#2a86d8}
.drawer-head span{display:block;font-weight:400;font-size:12px}
.drawer ul{list-style:none;font-size:11px}
.drawer li{height:34px;display:flex;align-items:center;padding-left:52px}
.drawer li.on{background:rgba(255,255,255,.18)}
.note{margin:12px 12px 0;border:1px solid #ddd;border-left:3px solid var(--blue);padding:6px 8px;font-size:11px;color:var(--blue)}
.note small{display:block;color:#888;font-size:9px}
.todo{margin:12px 10px 0;border:1px solid #ddd;padding:6px 8px;font-size:11px;height:104px;position:relative}
.todo .t{color:var(--blue);font-size:12px}
.todo .k{color:#888;font-size:9px}
.todo .a{font-size:9px;color:#333;margin-top:4px;display:flex;gap:4px}
.todo .m{font-size:16px;color:#333;margin-top:4px}
.todo .d{position:absolute;right:6px;bottom:4px;font-size:8px;color:#888}
.todo .flag{position:absolute;right:8px;top:8px}
.screens .btn{position:absolute;left:492px;top:614px;width:250px;height:54px;font-size:18px}

/* footer */
.footer-top{position:absolute;left:0;top:3100px;width:1200px;height:205px;background:var(--footer);color:#aaa}
.footer-top h4{font-size:11px;color:#fff;letter-spacing:.5px;font-weight:600}
.divider{position:absolute;left:602px;top:24px;width:1px;height:150px;background:#555}
.social{display:flex;gap:10px;margin-top:22px}
.social span{width:26px;height:26px;border-radius:50%;background:#3a86c8}
.subscribe-field{position:absolute;left:658px;top:122px;width:312px;height:36px;background:#eee}
.subscribe-btn{position:absolute;left:983px;top:122px;width:124px;height:36px;background:var(--green-dark);color:#fff;font-size:12px;font-weight:600;display:flex;align-items:center;justify-content:center}
.footer-bottom{position:absolute;left:0;top:3305px;width:1200px;height:295px;background:var(--footer-deep);color:#999;font-size:11px}
.footer-col{position:absolute;top:30px}
.footer-col h4{color:#fff;font-size:11px;font-weight:600;margin-bottom:22px;letter-spacing:.4px}
.footer-col li{list-style:none;height:26px}
.footer-col li::before{content:"› ";color:#666}
.contact-row{display:flex;align-items:center;gap:12px;margin-top:16px}
.contact-row i{width:18px;height:18px;background:#ccc;display:block}
.copyright{position:absolute;left:0;top:255px;width:1200px;text-align:center;font-size:10px;color:#777}
</style>
</head>
<body>

<header class="site-header">
  <div class="brand"><span class="brand-mark"></span><span class="brand-name">RV7</span></div>
  <nav class="nav"><span>HOME</span><span>ABOUT US</span><span>SERVICES</span><span>GALLERY</span><span>TEAM</span><span>TESTIMONIALS</span><span>CONTACT US</span></nav>
</header>

<section class="hero" role="img" aria-label="Office workers covering their faces amid smoke during an emergency evacuation">
  <h1 class="hero-title">Emergency , Command Control &amp; Co-ordination</h1>
  <a class="btn">Learn More</a>
</section>

<h2 class="section-title" style="top:800px">Why adopt RV7?</h2>
<ul class="why-list">
  <li><svg class="tick" viewBox="0 0 14 14"><path d="M2 7l3 3 7-7" fill="none" stroke="#7fae1f" stroke-width="2"/></svg>Easy system to register volunteers</li>
  <li><svg class="tick" viewBox="0 0 14 14"><path d="M2 7l3 3 7-7" fill="none" stroke="#7fae1f" stroke-width="2"/></svg>Accurate identification of number of CERT Volunteers available to help in an incident</li>
  <li><svg class="tick" viewBox="0 0 14 14"><path d="M2 7l3 3 7-7" fill="none" stroke="#7fae1f" stroke-width="2"/></svg>Efficient Communication mechanism to reach out to the volunteers via SMS</li>
  <li><svg class="tick" viewBox="0 0 14 14"><path d="M2 7l3 3 7-7" fill="none" stroke="#7fae1f" stroke-width="2"/></svg>Rich graphical visualization of Incidents &amp; Damages associated with the incidents</li>
  <li><svg class="tick" viewBox="0 0 14 14"><path d="M2 7l3 3 7-7" fill="none" stroke="#7fae1f" stroke-width="2"/></svg>Easy Management and Tracking of resources associated with</li>
  <li class="sub"><svg class="tick" viewBox="0 0 14 14"><path d="M2 7l3 3 7-7" fill="none" stroke="#7fae1f" stroke-width="2"/></svg>Incident</li>
  <li class="sub"><svg class="tick" viewBox="0 0 14 14"><path d="M2 7l3 3 7-7" fill="none" stroke="#7fae1f" stroke-width="2"/></svg>Team</li>
  <li class="sub"><svg class="tick" viewBox="0 0 14 14"><path d="M2 7l3 3 7-7" fill="none" stroke="#7fae1f" stroke-width="2"/></svg>Task</li>
  <li class="sub"><svg class="tick" viewBox="0 0 14 14"><path d="M2 7l3 3 7-7" fill="none" stroke="#7fae1f" stroke-width="2"/></svg>Supplies</li>
  <li class="sub"><svg class="tick" viewBox="0 0 14 14"><path d="M2 7l3 3 7-7" fill="none" stroke="#7fae1f" stroke-width="2"/></svg>Volunteers</li>
  <li><svg class="tick" viewBox="0 0 14 14"><path d="M2 7l3 3 7-7" fill="none" stroke="#7fae1f" stroke-width="2"/></svg>Capture Notes and pictures about situations being handled</li>
  <li><svg class="tick" viewBox="0 0 14 14"><path d="M2 7l3 3 7-7" fill="none" stroke="#7fae1f" stroke-width="2"/></svg>Easy one click notification to teams on the ground and team members on the same task</li>
  <li><svg class="tick" viewBox="0 0 14 14"><path d="M2 7l3 3 7-7" fill="none" stroke="#7fae1f" stroke-width="2"/></svg>One click social media integration with Chirpline, Snapgrid and Circlebook related to the Incident</li>
</ul>
<div class="why-image" role="img" aria-label="Yellow notebook labelled disaster plan lying on printed charts with glasses and a marker"></div>

<section class="tasks">
  <h2 class="section-title">Tasks Management</h2>
  <div class="task-card">
    <div class="task"><div class="task-photo" role="img" aria-label="Volunteers collecting debris in a park" style="background:linear-gradient(160deg,#6f8a45,#a9b98a)"></div><div class="task-name">Debris Collection</div></div>
    <div class="task"><div class="task-photo" role="img" aria-label="Inspector filling in a damage assessment form beside a damaged car" style="background:linear-gradient(160deg,#4a4d52,#a9acb0)"></div><div class="task-name">Damage Assessment</div></div>
    <div class="task"><div class="task-photo" role="img" aria-label="Volunteer packing supply boxes" style="background:linear-gradient(160deg,#c9a57e,#e7d6bf)"></div><div class="task-name">Supply Distribution</div></div>
    <div class="task"><div class="task-photo" role="img" aria-label="Volunteer in a white shirt embracing a resident" style="background:linear-gradient(160deg,#9c7a5c,#e6e1dc)"></div><div class="task-name">Custom Task</div></div>
  </div>
</section>

<h2 class="section-title" style="top:1916px">What we do</h2>
<p class="what-sub">City Officials and Emergency Management Officials can get access to instant statistics on</p>

<div class="feature" style="left:110px"><h3>INCIDENT MANAGEMENT</h3>
  <ul>
    <li><svg class="tick" viewBox="0 0 14 14"><path d="M2 7l3 3 7-7" fill="none" stroke="#222" stroke-width="2"/></svg>How many volunteers</li>
    <li><svg class="tick" viewBox="0 0 14 14"><path d="M2 7l3 3 7-7" fill="none" stroke="#222" stroke-width="2"/></svg>Volunteer hours</li>
    <li><svg class="tick" viewBox="0 0 14 14"><path d="M2 7l3 3 7-7" fill="none" stroke="#222" stroke-width="2"/></svg>Tasks Involved</li>
    <li><svg class="tick" viewBox="0 0 14 14"><path d="M2 7l3 3 7-7" fill="none" stroke="#222" stroke-width="2"/></svg>Supplies distributed</li>
    <li><svg class="tick" viewBox="0 0 14 14"><path d="M2 7l3 3 7-7" fill="none" stroke="#222" stroke-width="2"/></svg>Teams involved</li>
  </ul></div>
<div class="feature" style="left:445px"><h3>VOLUNTEER MANAGEMENT</h3>
  <ul>
    <li><svg class="tick" viewBox="0 0 14 14"><path d="M2 7l3 3 7-7" fill="none" stroke="#222" stroke-width="2"/></svg>Number of Volunteers</li>
    <li><svg class="tick" viewBox="0 0 14 14"><path d="M2 7l3 3 7-7" fill="none" stroke="#222" stroke-width="2"/></svg>Hours Spent</li>
    <li><svg class="tick" viewBox="0 0 14 14"><path d="M2 7l3 3 7-7" fill="none" stroke="#222" stroke-width="2"/></svg>Type of tasks Involved in</li>
    <li><svg class="tick" viewBox="0 0 14 14"><path d="M2 7l3 3 7-7" fill="none" stroke="#222" stroke-width="2"/></svg>Team Efficiency</li>
  </ul></div>
<div class="feature" style="left:790px"><h3>DAMAGE ASSESSMENT</h3>
  <ul>
    <li><svg class="tick" viewBox="0 0 14 14"><path d="M2 7l3 3 7-7" fill="none" stroke="#222" stroke-width="2"/></svg>What kind of damage</li>
    <li><svg class="tick" viewBox="0 0 14 14"><path d="M2 7l3 3 7-7" fill="none" stroke="#222" stroke-width="2"/></svg>Location of damage</li>
    <li><svg class="tick" viewBox="0 0 14 14"><path d="M2 7l3 3 7-7" fill="none" stroke="#222" stroke-width="2"/></svg>Notes/Pictures</li>
    <li><svg class="tick" viewBox="0 0 14 14"><path d="M2 7l3 3 7-7" fill="none" stroke="#222" stroke-width="2"/></svg>Time taken to clean up the damage</li>
  </ul></div>

<section class="screens">
  <h2 class="section-title">Volunteer Mobile Screens</h2>

  <div class="phone" style="left:216px;width:244px;height:438px;background:#7a7a7a">
    <div class="drawer">
      <div class="statusbar" style="background:#1560a8"></div>
      <div class="drawer-head">Dana Ruelle<span>Volunteer</span></div>
      <ul>
        <li>Dashboard</li><li class="on">Notifications</li><li>Profile</li><li>TODO List</li>
        <li>Directory</li><li>Help</li><li>Share</li><li>Logout</li>
      </ul>
    </div>
  </div>

  <div class="phone" style="left:490px;width:210px;height:438px">
    <div class="statusbar" style="background:#1560a8">2:22 PM</div>
    <div class="appbar" style="padding-left:14px">Notifications</div>
    <div class="note">Impending Weather Conditions<small>Impending Weather Conditions</small></div>
    <div class="note">Incoming Storms. Wrap up in 1...<small>Incoming Storms. Wrap up in 10 min</small></div>
  </div>

  <div class="phone" style="left:768px;width:252px;height:438px">
    <div class="statusbar" style="background:#1560a8">7:12 PM</div>
    <div class="appbar" style="padding-left:14px">TODO List</div>
    <div class="todo"><svg class="flag" width="12" height="11"><path d="M6 0l6 11H0z" fill="#f0a020"/></svg>
      <div class="t">good Task</div><div class="k">Supply Distribution</div>
      <div class="a"><svg width="8" height="10"><path d="M4 0a4 4 0 0 1 4 4c0 3-4 6-4 6S0 7 0 4a4 4 0 0 1 4-4z" fill="#e33"/></svg>Mesa Ridge Rd, Pinecrest, AZ 85000</div>
      <div class="m">23 Min</div><div class="d">Apr 28, 2016 08:29 AM</div></div>
    <div class="todo"><svg class="flag" width="12" height="11"><path d="M6 0l6 11H0z" fill="#3a9a4a"/></svg>
      <div class="t">Find damage areas</div><div class="k">Damage Assessment</div>
      <div class="a"><svg width="8" height="10"><path d="M4 0a4 4 0 0 1 4 4c0 3-4 6-4 6S0 7 0 4a4 4 0 0 1 4-4z" fill="#e33"/></svg>Old Mill Rd, Brookfall, Harwin</div>
      <div class="m">40 Min</div><div class="d">May 12, 2016 01:26 AM</div></div>
    <div class="todo"><svg class="flag" width="12" height="11"><path d="M6 0l6 11H0z" fill="#3a9a4a"/></svg>
      <div class="t">Supply Food</div><div class="k">Supply Distribution</div>
      <div class="a"><svg width="8" height="10"><path d="M4 0a4 4 0 0 1 4 4c0 3-4 6-4 6S0 7 0 4a4 4 0 0 1 4-4z" fill="#e33"/></svg>1180 Cedarline Rd, Fairmont, TX 75...</div>
      <div class="m">40 Min</div><div class="d">Jul 11, 2016 07:10 PM</div></div>
  </div>

  <a class="btn">View more screens</a>
</section>

<footer>
  <div class="footer-top">
    <div class="abs" style="left:104px;top:34px;width:440px">
      <h4>CONNECT WITH US</h4>
      <p style="font-size:11px;margin-top:20px;line-height:16px">The roles from CERT teams have been created to have access to either the web, mobile or both the interfaces</p>
      <div class="social"><span></span><span></span><span></span><span></span><span></span></div>
    </div>
    <div class="divider"></div>
    <div class="abs" style="left:658px;top:34px;width:460px">
      <h4>SUBSCRIBE A NEWSLETTER</h4>
      <p style="font-size:11px;margin-top:20px">Subscribe to our newsletter to NORTHVALE first for our special offers!</p>
    </div>
    <div class="subscribe-field"></div>
    <div class="subscribe-btn">SUBSCRIBE</div>
  </div>

  <div class="footer-bottom">
    <div class="footer-col" style="left:104px"><h4>INFORMATION</h4>
      <ul><li>Services</li><li>Gallery</li><li>Team</li><li>Testimonials</li><li>Contact Us</li></ul></div>
    <div class="footer-col" style="left:360px"><h4>SERVICES</h4>
      <ul><li>Incident Management</li><li>Volunteer Management</li><li>Damage Assessment</li><li>Task Management</li><li>Team Management</li></ul></div>
    <div class="footer-col" style="left:614px"><h4>TASKS MANAGEMENT</h4>
      <ul><li>Debris Collection</li><li>Damage Assessment</li><li>Supply Distribution</li><li>Custom Task</li></ul></div>
    <div class="footer-col" style="left:868px;width:240px"><h4>ABOUT</h4>
      <p style="line-height:15px">City Officials and Emergency Management Officials can get access to instant statistics on</p>
      <div class="contact-row" style="margin-top:24px"><i></i>555-014-2290</div>
      <div class="contact-row"><i></i>hello@rv7ops.net</div>
    </div>
    <p class="copyright">Copyright 2016 RV7. All Rights reserved.</p>
  </div>
</footer>

</body>
</html>
```